Werbetafel für Immobilienverwaltung
Zielgruppe
Wir sind im Kern eine Immobilienverwaltung, daher richten wir uns an Eigentümer/Investoren/Kapitalanleger. Neben der Verwaltung welche auch durch Hausmeisterservice (Grünarbeiten usw.) erweitert werden kann, bieten wir die Gutachtenerstellung sowie den Vertrieb (Maklertätigkeit in Verkauf sowie Vermietung) an.
Ein großer Vorteil ist unsere Digitale Arbeitsweise (noch keine Selbstverständlichkeit in der Branche).
Aufgabenstellung
Ziel ist es, das Unternehmen unaufdringlich jedoch wirksam und informativ auf einer Werbetafel zu präsentieren.
Maße der Tafel, welche sich im ausgangsbereich eines großen Lebensmittelunternehmens befindet, ist B 320cm x H 120cm.
Die Kundschaft läuft in ca. 1m Entfernung an der Tafel vorbei, sie sollte also von nahem nicht zu überrumpelt wirken.
Unser Logo sowie Telefonnummer sollte iwie untergebracht werden.
Gern auch eigene Ideen umsetzen falls Ihr welche habt.

```html
<!DOCTYPE html>
<html lang="de">
<head>
<meta charset="utf-8">
<title>Nordlicht Verwaltung – Werbetafel</title>
<link href="https://fonts.googleapis.com/css2?family=Poppins:wght@300;400;700;800&display=swap" rel="stylesheet">
<style>
  :root {
    --red: #9a2222;
    --black: #050505;
    --white: #ffffff;
    --paper: #fdfbfa;
    --ink: #111111;
    --teal: #1d5d78;
    --logo-grey: #6f6f6a;
    --page: #ffffff;
  }
  * { margin: 0; padding: 0; box-sizing: border-box; }
  html, body {
    width: 1200px; height: 849px; overflow: hidden;
    background: var(--page);
    font-family: "Poppins", sans-serif;
  }
  .board {
    position: absolute; left: 65px; top: 46px;
    width: 1070px; height: 757px;
    background: var(--white);
    box-shadow: 6px 6px 10px rgba(0,0,0,.45);
    overflow: hidden;
  }
  .hero-photo {
    position: absolute; left: 0; top: 0; width: 1070px; height: 294px;
    background:
      linear-gradient(180deg, #3c3c3c 0%, #777 28%, #8a8a8a 45%, #3d3d3d 62%, #5a5a5a 78%, #2b2b2b 100%);
  }
  .logo-panel { position: absolute; left: 42px; top: 0; width: 226px; height: 273px; }
  .logo-name {
    position: absolute; left: 42px; top: 96px; width: 226px;
    text-align: center; color: var(--logo-grey);
    font-weight: 700; font-size: 22px; letter-spacing: 2px; line-height: 1.2;
  }
  .logo-name .mark {
    display: block; width: 14px; height: 14px; margin: 0 auto 10px;
    background: var(--red);
  }
  .band { position: absolute; left: 0; width: 1070px; height: 8px; background: var(--red); }
  .band.top { top: 294px; }
  .band.bottom { top: 604px; }
  .headline {
    position: absolute; left: 36px; top: 348px;
    font-weight: 800; font-size: 51px; letter-spacing: 4.5px;
    color: var(--ink); line-height: 1;
  }
  .subline {
    position: absolute; left: 37px; top: 413px;
    font-weight: 300; font-size: 41px; letter-spacing: 3.8px;
    color: var(--ink); line-height: 1;
  }
  .mission {
    position: absolute; left: 40px; top: 489px; width: 459px;
    font-weight: 300; font-size: 13.8px; line-height: 16.3px;
    text-align: justify; color: var(--ink);
  }
  .service { position: absolute; display: flex; align-items: center; }
  .service svg { width: 48px; height: 48px; flex: none; }
  .service span {
    position: absolute; left: 75px; white-space: nowrap;
    color: var(--red); font-weight: 700; font-size: 21px;
  }
  .s1 { left: 597px; top: 372px; }
  .s2 { left: 841px; top: 370px; }
  .s3 { left: 597px; top: 464px; }
  .s4 { left: 841px; top: 464px; }
  .footer {
    position: absolute; left: 0; top: 612px; width: 1070px; height: 145px;
    background: var(--black);
  }
  .contact { position: absolute; top: 54px; display: flex; }
  .contact .icon {
    width: 47px; height: 47px; background: var(--red);
    display: flex; align-items: center; justify-content: center;
  }
  .contact .text {
    position: absolute; top: -5px; white-space: nowrap;
    color: var(--white); font-weight: 300; font-size: 22.5px; line-height: 27px;
  }
  .c1 { left: 35px; } .c1 .text { left: 70px; }
  .c2 { left: 385px; } .c2 .text { left: 76px; }
  .c3 { left: 784px; } .c3 .text { left: 76px; }
</style>
</head>
<body>
<div class="board">
  <div class="hero-photo" role="img" aria-label="Schwarz-weiß Stadtpanorama am Abend mit Dom, Hubbrücke über den Fluss und Bäumen am Ufer"></div>

  <svg class="logo-panel" viewBox="0 0 226 273" aria-hidden="true">
    <polygon points="0,0 226,0 226,227 0,188" fill="var(--paper)"/>
  </svg>
  <div class="logo-name"><span class="mark"></span>NORDLICHT<br>VERWALTUNG</div>

  <div class="band top"></div>

  <h1 class="headline">IHRE IMMOBILIE</h1>
  <p class="subline">UNSER KNOW-HAUS</p>
  <p class="mission">Unsere Mission: Keine lästigen Papierunterlagen mehr, kein Warten auf den Briefträger – denn bei uns können Sie von jedem Ort der Welt und nahezu jedem Endgerät auf Ihre Unterlagen zugreifen und diese auf Wunsch sogar versenden. Das klingt nicht nur gut, sondern ist es auch!</p>

  <div class="service s1">
    <svg viewBox="0 0 48 48" fill="none" stroke="var(--teal)" stroke-width="1.6">
      <path d="M24 26 C16 16 15 12 17 8 a8 8 0 0 1 14 0 C33 12 32 16 24 26Z"/>
      <circle cx="24" cy="11" r="3.5"/>
      <path d="M17 22 L9 22 L2 36 L46 36 L39 22 L31 22"/>
    </svg>
    <span>Grundstuck</span>
  </div>
  <div class="service s2">
    <svg viewBox="0 0 48 48" fill="none" stroke="var(--teal)" stroke-width="1.4">
      <rect x="22" y="2" width="24" height="44"/>
      <rect x="26" y="7" width="5" height="4"/><rect x="36" y="7" width="5" height="4"/>
      <rect x="26" y="16" width="5" height="4"/><rect x="36" y="16" width="5" height="4"/>
      <rect x="26" y="25" width="5" height="4"/><rect x="36" y="25" width="5" height="4"/>
      <rect x="2" y="30" width="20" height="16"/>
      <path d="M1 30 L4 24 L22 24" />
      <rect x="5" y="35" width="5" height="5"/><rect x="13" y="37" width="5" height="9"/>
    </svg>
    <span>Gewerbe</span>
  </div>
  <div class="service s3">
    <svg viewBox="0 0 48 48" fill="none" stroke="var(--teal)" stroke-width="1.4">
      <rect x="4" y="2" width="40" height="44"/>
      <rect x="4" y="15" width="40" height="10" fill="#f0d8c8"/>
      <rect x="9" y="6" width="6" height="4"/><rect x="21" y="6" width="6" height="4"/><rect x="33" y="6" width="6" height="4"/>
      <rect x="9" y="30" width="6" height="4"/><rect x="21" y="30" width="6" height="4"/><rect x="33" y="30" width="6" height="4"/>
      <rect x="20" y="38" width="7" height="8"/>
      <line x1="0" y1="46" x2="48" y2="46"/>
    </svg>
    <span>Wohnung</span>
  </div>
  <div class="service s4">
    <svg viewBox="0 0 48 48" fill="none" stroke="var(--teal)" stroke-width="1.4">
      <path d="M2 22 L12 8 L36 8 L46 22 Z" fill="#c9c9c9"/>
      <rect x="13" y="3" width="4" height="5"/>
      <rect x="6" y="22" width="36" height="22"/>
      <rect x="10" y="28" width="7" height="6"/><rect x="31" y="28" width="7" height="6"/>
      <rect x="20" y="30" width="8" height="14"/>
      <line x1="2" y1="45" x2="46" y2="45"/>
    </svg>
    <span>Haus</span>
  </div>

  <div class="band bottom"></div>

  <div class="footer">
    <div class="contact c1">
      <div class="icon">
        <svg width="30" height="20" viewBox="0 0 30 20"><rect x="1" y="1" width="28" height="18" fill="none" stroke="#fff" stroke-width="2"/><path d="M1 1 L15 12 L29 1 M1 19 L11 9 M29 19 L19 9" fill="none" stroke="#fff" stroke-width="2"/></svg>
      </div>
      <div class="text">info@nordlicht-hv.de<br>www.nordlicht-hv.de</div>
    </div>
    <div class="contact c2">
      <div class="icon">
        <svg width="30" height="28" viewBox="0 0 30 28"><path d="M15 2 L1 15 L4 17 L15 7 L26 17 L29 15 Z" fill="#fff"/><path d="M6 16 L15 8 L24 16 L24 27 L18 27 L18 19 L12 19 L12 27 L6 27 Z" fill="#fff"/></svg>
      </div>
      <div class="text">Lindenhofstr. 17<br>39112 Elbstadt</div>
    </div>
    <div class="contact c3">
      <div class="icon">
        <svg width="26" height="28" viewBox="0 0 26 28"><path d="M6 2 L10 8 L8 11 C9 15 12 19 15 21 L18 19 L24 23 L21 27 C12 27 2 15 2 6 Z" fill="#fff"/></svg>
      </div>
      <div class="text">0391-48 27 305<br>0160-55 12 73 9</div>
    </div>
  </div>
</div>
</body>
</html>
```